Diverse, up-scale salon needs eye-catching, unique business cards.

We are looking for a unique business card design for our stylist but that can also be multi functional and used for appointment reminder and referrals. I will need a design in a format that I can modify names and titles going forward. In the past we have had a dark background with the logo on one side, and stylist and contact information on the other but we are open to all ideas. I have included our mission statement as well as branded colors below. The statement doesn't need to go on the card, it's just a reference for target market. We need space for the stylists name, title, instagram handle and then the salons phone number, website and address. I am also open to adding a spot for a qr code linked to the stylist instagram or the salon booking link.

primary brand colors:
#333333 #233415 #36502a #93874a #000000
Mission statement:
Vessolin Hair Studio, a high-end salon located in the lively Downtown Farmington, Michigan, is committed to providing exceptional services in a welcoming and relaxed environment to meet the needs of our diverse clientele.
Our salon specializes in contemporary custom haircuts, coloring, extensions, and barbering and beard grooming services. Our team of skilled stylists is passionate and inventive in their hair styling techniques. At the heart of our salon are values centered on quality, innovation, creativity, and above all, comfort. These core values are evident in every appointment across our customizable array of services.
Our goal is to establish a benchmark for exceptional hair care for every human.
Website: www.vessolinhairstudio.example
instagram: @vessolinhairstudio
address: 41782 Pelham Crest Rd, Marlowe Bay OR
phone: 555-613-4087

Industry/Entity Type

Hair Salon

Contact Information for Business Card

Stylist name, title, phone, instagram, website, address, (optional qr code)

Requirements
Should not have
• Does not need mission statement on the card.

```html
<!DOCTYPE html>
<html lang="en">
<head>
<meta charset="UTF-8">
<title>Vessolin Hair Studio — Business Card</title>
<link href="https://fonts.googleapis.com/css2?family=Montserrat:wght@400;500;800&display=swap" rel="stylesheet">
<style>
  :root {
    --backdrop: #d3d7d8;
    --card-dark: #231f20;
    --olive: #93874a;
    --white: #ffffff;
    --edge: #2a9cc4;
  }
  * { box-sizing: border-box; margin: 0; padding: 0; }
  html, body { width: 1200px; height: 1200px; overflow: hidden; }
  body {
    background: var(--backdrop);
    font-family: "Montserrat", sans-serif;
    display: flex;
    flex-direction: column;
    align-items: center;
    justify-content: center;
    gap: 60px;
  }
  .card {
    width: 840px;
    height: 480px;
    position: relative;
    overflow: hidden;
    box-shadow: 0 14px 30px rgba(0,0,0,0.18);
    border-bottom: 3px solid var(--edge);
  }
  .card--front { background: var(--card-dark); }
  .card--back {
    background: var(--olive);
    display: flex;
    align-items: center;
    justify-content: center;
  }

  .brand-mark {
    display: flex;
    align-items: center;
    gap: 16px;
    font-weight: 800;
    text-transform: uppercase;
    letter-spacing: 0.08em;
    line-height: 1.15;
  }
  .brand-mark__dot {
    width: 26px; height: 26px;
    border-radius: 50%;
    flex: none;
  }
  .card--front .brand-mark {
    position: absolute;
    left: 60px; top: 150px;
    width: 300px;
    color: var(--olive);
    font-size: 30px;
  }
  .card--front .brand-mark__dot { border: 3px solid var(--olive); }
  .card--back .brand-mark { color: var(--white); font-size: 44px; }
  .card--back .brand-mark__dot { border: 4px solid var(--white); width: 38px; height: 38px; }

  .divider {
    position: absolute;
    left: 392px; top: 60px;
    width: 2px; height: 290px;
    background: var(--white);
  }

  .contact {
    position: absolute;
    left: 430px; top: 64px;
    color: var(--white);
  }
  .contact__name {
    color: var(--olive);
    font-weight: 800;
    font-size: 36px;
    line-height: 1.1;
  }
  .contact__title { font-size: 20px; margin-top: 4px; }
  .contact__address { font-size: 19px; margin-top: 20px; line-height: 1.3; }
  .contact__list { list-style: none; margin-top: 14px; font-size: 19px; line-height: 1.55; }
  .contact__list li { display: flex; align-items: center; gap: 10px; }
  .contact__list svg { width: 18px; height: 18px; flex: none; }

  .social-band {
    position: absolute;
    left: 0; right: 0; bottom: 0;
    height: 68px;
    background: var(--olive);
    display: flex;
    align-items: center;
    justify-content: space-around;
    color: var(--white);
    font-size: 19px;
  }
  .social-band__item { display: flex; align-items: center; gap: 10px; }
  .social-band__dot {
    width: 16px; height: 16px;
    border-radius: 50%;
    background: var(--card-dark);
  }
</style>
</head>
<body>

  <section class="card card--front" aria-label="Business card front">
    <div class="brand-mark">
      <span class="brand-mark__dot"></span>
      <span>Vessolin Hair Studio</span>
    </div>

    <div class="divider"></div>

    <div class="contact">
      <h1 class="contact__name">Vessolin</h1>
      <p class="contact__title">Founder &amp; Director</p>
      <p class="contact__address">41782 Pelham Crest Rd,<br>Marlowe Bay OR</p>
      <ul class="contact__list">
        <li>
          <svg viewBox="0 0 24 24" aria-hidden="true"><path fill="#93874a" d="M6.6 10.8a15.1 15.1 0 0 0 6.6 6.6l2.2-2.2c.3-.3.7-.4 1-.2 1.1.4 2.3.6 3.6.6.6 0 1 .4 1 1V20c0 .6-.4 1-1 1A17 17 0 0 1 3 4c0-.6.4-1 1-1h3.5c.6 0 1 .4 1 1 0 1.3.2 2.5.6 3.6.1.3 0 .7-.2 1z"/></svg>
          555-613-4087
        </li>
        <li>
          <svg viewBox="0 0 24 24" aria-hidden="true"><path fill="#93874a" d="M2 5h20v14H2z"/><path fill="none" stroke="#231f20" stroke-width="1.8" d="M2 5l10 8 10-8"/></svg>
          hello@vessolinhairstudio.example
        </li>
        <li>
          <svg viewBox="0 0 24 24" aria-hidden="true"><circle cx="12" cy="12" r="10" fill="#93874a"/><path fill="none" stroke="#231f20" stroke-width="1.5" d="M2 12h20M12 2c3 3 3 17 0 20M12 2c-3 3-3 17 0 20"/></svg>
          www.vessolinhairstudio.example
        </li>
      </ul>
    </div>

    <div class="social-band">
      <span class="social-band__item"><span class="social-band__dot"></span>@vessolinhairstudio</span>
      <span class="social-band__item"><span class="social-band__dot"></span>@vessolinhairstudio</span>
    </div>
  </section>

  <section class="card card--back" aria-label="Business card back">
    <div class="brand-mark">
      <span class="brand-mark__dot"></span>
      <span>Vessolin Hair Studio</span>
    </div>
  </section>

</body>
</html>
```